MRT Property - Business Cards

Looking for a business card & general letterhead, signage etc design for our new logo.

Colours:
000a20
0056a2
00b5ef
0088ce
68cef2

Fonts:
Poppins
Karla

Please keep look and feel of new brand - example in the zip package I sent.

```html
<!DOCTYPE html>
<html lang="en">
<head>
<meta charset="UTF-8">
<title>MRT Property – Business Cards</title>
<link rel="stylesheet" href="https://fonts.googleapis.com/css2?family=Poppins:wght@600&family=Montserrat:wght@400&family=Kalam:wght@300&display=swap">
<style>
  :root {
    --ink: #000a20;
    --card-dark: #121527;
    --brand-blue: #0056a2;
    --brand-royal: #0b57a4;
    --sky: #00b5ef;
    --mid-blue: #0088ce;
    --light-blue: #68cef2;
    --white: #ffffff;
    --backdrop: #9b9b9b;
  }
  * { margin: 0; padding: 0; box-sizing: border-box; }
  html, body { width: 1093px; height: 1200px; overflow: hidden; }
  body { background: var(--backdrop); position: relative; font-family: "Montserrat", sans-serif; }

  .card {
    position: absolute;
    left: 265px;
    width: 580px;
    border-radius: 18px;
    overflow: hidden;
  }
  .card--front { top: 225px; height: 363px; background: var(--card-dark); }
  .card--back { top: 616px; height: 366px; background: var(--brand-royal); }

  .brand-graphic {
    position: absolute;
    left: 0; top: 0;
    width: 300px; height: 363px;
    background: radial-gradient(ellipse 85% 70% at 25% 50%, rgba(0,136,206,0.85) 0%, rgba(0,136,206,0.45) 45%, rgba(18,21,39,0) 100%);
  }

  .wordmark__name, .wordmark__sub {
    position: absolute;
    font-family: "Poppins", sans-serif;
    font-weight: 600;
    line-height: 1;
    white-space: nowrap;
  }
  .card--front .wordmark__name { left: 299px; top: 20px; font-size: 98px; letter-spacing: -2px; color: var(--brand-blue); }
  .card--front .wordmark__sub { left: 303px; top: 107px; font-size: 21px; letter-spacing: 10px; color: var(--brand-blue); }

  .brand-dot {
    position: absolute;
    left: 105px; top: 140px;
    width: 92px; height: 92px;
    border-radius: 50%;
    background: var(--light-blue);
  }
  .card--back .wordmark__name { left: 222px; top: 117px; font-size: 132px; letter-spacing: -4px; color: var(--white); }
  .card--back .wordmark__sub { left: 232px; top: 238px; font-size: 28px; letter-spacing: 14px; color: var(--white); }

  .holder__name { position: absolute; left: 303px; top: 147px; font-family: "Kalam", cursive; font-weight: 300; font-size: 30px; line-height: 1; color: var(--brand-blue); }
  .holder__role { position: absolute; left: 305px; top: 184px; font-size: 13px; line-height: 1; color: var(--white); }

  .address { position: absolute; left: 305px; top: 216px; font-size: 13.5px; line-height: 16px; color: var(--white); font-style: normal; }

  .contacts { position: absolute; left: 305px; top: 268px; list-style: none; }
  .contacts li { display: flex; align-items: center; height: 24.5px; font-size: 13px; color: var(--white); }
  .contacts svg { width: 13px; height: 13px; margin-right: 8px; flex: none; }
</style>
</head>
<body>

  <section class="card card--front" aria-label="Business card front">
    <div class="brand-graphic" role="img" aria-label="Brand graphic area"></div>

    <span class="wordmark__name">MRT</span>
    <span class="wordmark__sub">PROPERTY</span>

    <p class="holder__name">Daniel Reyes</p>
    <p class="holder__role">Managing Director</p>

    <address class="address">245 Harbor Point Lane<br>Brookfield, OR 97204</address>

    <ul class="contacts">
      <li>
        <svg viewBox="0 0 16 16" aria-hidden="true"><path fill="var(--mid-blue)" d="M3.6 1.5l2.3 2.6-1.2 1.8c.9 2 2.5 3.6 4.5 4.5l1.8-1.2 2.6 2.3-1.3 2.4C7 13.4 2.6 9 1.2 2.8z"/></svg>
        555.310.4726
      </li>
      <li>
        <svg viewBox="0 0 16 16" aria-hidden="true"><rect x="1" y="3" width="14" height="10" rx="1" fill="var(--mid-blue)"/><path d="M1.5 4l6.5 5 6.5-5" stroke="var(--card-dark)" stroke-width="1.3" fill="none"/></svg>
        info@mrtproperty.com
      </li>
      <li>
        <svg viewBox="0 0 16 16" aria-hidden="true"><circle cx="8" cy="8" r="7" fill="var(--mid-blue)"/><path d="M1 8h14M8 1c-3 3-3 11 0 14M8 1c3 3 3 11 0 14" stroke="var(--card-dark)" stroke-width="1" fill="none"/></svg>
        www.mrtproperty.com
      </li>
    </ul>
  </section>

  <section class="card card--back" aria-label="Business card back">
    <span class="brand-dot" aria-hidden="true"></span>
    <span class="wordmark__name">MRT</span>
    <span class="wordmark__sub">PROPERTY</span>
  </section>

</body>
</html>
```